Website for new dental office

I am Dr. Colin Ashford and am building a new dental practice. I specialize in general dentistry. I am young and have a higher end dental practice incorporating very new technologies and would like my website to reflect that. As many dental patients are older, the website must be very easy to navigate. I would like patients to be able to request appointments, and will eventually add on patient information forms (the health history, etc, that you normally fill out in the practice) from my practice management software, so leave an area for that.

Industry/Entity Type

Building

```html
<!DOCTYPE html>
<html lang="en">
<head>
<meta charset="utf-8">
<title>Ashford Dental Clinic</title>
<link rel="stylesheet" href="https://fonts.googleapis.com/css2?family=Cinzel:wght@400;700&family=Open+Sans:wght@400;600&family=Yanone+Kaffeesatz:wght@400;600&family=Comfortaa:wght@500&display=swap">
<style>
:root{
  --orange:#f26a1b;
  --orange-light:#ff8a3a;
  --grey-text:#6f7f86;
  --dark:#2b2b2b;
  --body:#333;
  --panel:#ffffff;
  --page:#e3ecef;
  --hero-a:#a9b4b8;
  --hero-b:#6f7c81;
  --gold:#f9c24c;
  --band:#3a2f22;
  --field-border:#d4d9dc;
}
*{box-sizing:border-box;margin:0;padding:0}
html,body{width:1200px;height:1200px;overflow:hidden}
body{position:relative;font-family:"Open Sans",sans-serif;color:var(--body);
  background:radial-gradient(ellipse at 50% 60%,#f7fafb 0%,var(--page) 70%,#c9d6db 100%)}
.abs{position:absolute}
.topbar{left:0;top:0;width:1200px;height:8px;background:#75858b}
.header{left:0;top:8px;width:1200px;height:146px;background:linear-gradient(90deg,#e6ecee,#fff 30%,#fff 70%,#dfe6e9)}
.brand{left:124px;top:66px;font-family:"Open Sans",sans-serif;font-weight:400;font-size:30px;color:var(--grey-text);letter-spacing:-.5px}
.today{left:908px;top:16px;width:70px;height:28px;border-radius:50%;background:var(--gold);
  font-family:"Comfortaa",cursive;font-size:13px;color:#a3461a;text-align:center;line-height:28px}
.callout{right:150px;top:46px;font-family:"Yanone Kaffeesatz",sans-serif;font-weight:600;font-size:28px;color:var(--grey-text)}
.nav{left:489px;top:96px;width:570px;height:37px;border-radius:6px;
  background:linear-gradient(#ff8a3a,#f0601a);display:flex;align-items:center;padding-left:36px}
.nav a{font-size:14px;color:#fff;text-decoration:none;padding:0 15px;line-height:37px}
.nav a.active{background:#fff;color:#555;border-radius:4px 4px 0 0;height:33px;line-height:33px;margin-top:4px;padding:0 9px}
.hero{left:0;top:154px;width:1200px;height:380px;background:radial-gradient(ellipse at 75% 40%,#cdd4d6 0%,var(--hero-a) 40%,var(--hero-b) 100%)}
.hero-photo{left:96px;top:154px;width:456px;height:380px;background:radial-gradient(ellipse at 50% 45%,#e9c7ae 0%,#d9a98c 55%,rgba(150,130,115,0) 78%)}
.search{left:746px;top:174px;width:245px;height:28px;background:#fff;border-radius:6px;
  font-family:"Yanone Kaffeesatz",sans-serif;font-weight:600;font-size:18px;color:#555;padding-left:13px;line-height:28px}
.search svg{position:absolute;right:6px;top:3px}
.hero-title{left:606px;top:276px;font-family:"Cinzel",serif;font-weight:400;font-size:32px;color:#fff}
.hero-sub{left:608px;top:320px;font-family:"Comfortaa",cursive;font-weight:500;font-size:26px;color:#151515}
.hero-text{left:606px;top:362px;width:360px;font-size:13px;line-height:22px;color:#fff}
.btn-learn{left:831px;top:438px;width:129px;height:37px;border-radius:7px;background:linear-gradient(#fff,#e6eaeb);
  font-family:"Yanone Kaffeesatz",sans-serif;font-weight:600;font-size:20px;color:#6f7f86;text-align:center;line-height:37px;box-shadow:0 3px 5px rgba(0,0,0,.25)}
.panel{left:139px;top:534px;width:922px;height:416px;background:var(--panel);box-shadow:0 2px 6px rgba(0,0,0,.08)}
.h-section{font-family:"Cinzel",serif;font-size:19px;color:var(--orange)}
.h-section .dk{color:#3a3a3a}
.welcome-photo{left:164px;top:602px;width:170px;height:256px;border:1px solid #f0a05a;background:linear-gradient(160deg,#b9d8ee 0%,#e4c2a4 55%,#6a4a35 100%)}
.welcome-text{left:351px;top:606px;width:194px;font-size:11.5px;line-height:22.2px;text-align:justify;hyphens:auto;-webkit-hyphens:auto;color:#222}
.btn-gold{border-radius:7px;background:linear-gradient(#ffd77a,var(--gold));color:#5a3a12;font-size:15px;text-align:center;box-shadow:0 3px 4px rgba(0,0,0,.15)}
.divider{left:581px;top:565px;width:1px;height:305px;background:#d8d8d8}
.field{border:1px solid var(--field-border);border-radius:7px;background:#fff;font-size:12px;color:#666;padding-left:12px;line-height:25px;height:27px;box-shadow:0 3px 3px -2px rgba(0,0,0,.12)}
.pref-on{left:603px;top:746px;width:98px;height:40px;border-radius:7px;background:linear-gradient(var(--orange-light),var(--orange));color:#fff;font-size:12px;line-height:17px;padding:4px 0 0 13px}
.pref-off{left:723px;top:748px;font-size:12px;line-height:17px;color:#666}
.smile{left:839px;top:570px;width:194px;height:164px;border:1px solid #f0a05a;background:linear-gradient(135deg,#5c4030,#c99478 45%,#8a5b40)}
.smile-band{left:840px;top:690px;width:192px;height:32px;background:rgba(30,30,30,.82);font-family:"Cinzel",serif;font-size:14px;color:#fff;line-height:32px;padding-left:16px}
.offer{left:839px;top:753px;width:194px;height:164px;background:linear-gradient(#ffe4a6,#f9bf49)}
.offer-text{left:850px;top:766px;width:184px;font-family:"Open Sans",sans-serif;font-weight:600;font-size:17px;letter-spacing:-.3px;line-height:28px;color:#4e3a21}
.offer-band{left:839px;top:871px;width:194px;height:31px;background:var(--band);font-family:"Cinzel",serif;font-size:14px;color:#fff;text-align:center;line-height:31px}
.h-foot{font-family:"Cinzel",serif;font-size:21px;color:#2f2f2f}
.links{font-size:11.5px;line-height:22.2px;color:#333;list-style:none}
.quote{left:505px;top:1011px;width:259px;font-size:11.5px;line-height:22.2px;text-align:justify;hyphens:auto;-webkit-hyphens:auto;color:#222}
.qmark{font-family:"Cinzel",serif;font-size:46px;color:#cfd3d5;line-height:1}
.social{left:849px;width:36px;height:36px;border:1px solid #c9cfd2;border-radius:5px;background:#fff}
.social-name{left:899px;font-size:15px;color:#555}
.footer{left:0;top:1166px;width:1200px;height:34px;background:#c7d3d7;font-size:10px;color:#444;text-align:center;line-height:32px}
</style>
</head>
<body>
<div class="abs header"></div>
<div class="abs topbar"></div>
<div class="abs brand">Ashford Dental Clinic</div>
<div class="abs today">Today!</div>
<div class="abs callout">Call For An Appointment : 0800 317 482</div>
<nav class="abs nav">
  <a class="active" href="#">HOME</a><a href="#">NEWS AND EVENTS</a><a href="#">SERVICES</a><a href="#">THE TEAM</a><a href="#">CONTACT US</a>
</nav>

<section class="abs hero"></section>
<div class="abs hero-photo" role="img" aria-label="Close-up portrait of a smiling woman with bright teeth"></div>
<div class="abs search">SEARCH
  <svg width="38" height="26" viewBox="0 0 38 26"><circle cx="17" cy="11" r="8.5" fill="#f4f6f7" stroke="#9aa4a8" stroke-width="2"/><line x1="23" y1="17" x2="33" y2="24" stroke="#7c878b" stroke-width="4" stroke-linecap="round"/></svg>
</div>
<h1 class="abs hero-title">Neque porro quisquam</h1>
<h2 class="abs hero-sub">bonorum et malorum</h2>
<p class="abs hero-text">Dr. Colin Ashford is specialised in gen<br>He provides higher end dental practice incorporating very<br>new technologies.eral dentistry</p>
<div class="abs btn-learn">LEARN MORE</div>

<main class="abs panel"></main>
<h3 class="abs h-section" style="left:164px;top:564px">Welcome to <span class="dk">Ashford</span> Dental Clinic</h3>
<div class="abs welcome-photo" role="img" aria-label="Smiling mother and young daughter against a blue sky"></div>
<p class="abs welcome-text" lang="en">Sed ut perspiciatis unde omnis iste natus error sit voluptatem accusantium doloremque laudantium, totam rem aperiam, eaque ipsa quae ab illo inventore veritatis et quasi architecto beatae vitae dicta sunt explicabo. Nemo enim ipsam voluptatem quia voluptas sit aspernatur aut odit aut fugit, sed quia consequuntur magni dolores eos</p>
<div class="abs btn-gold" style="left:477px;top:842px;width:71px;height:24px;line-height:24px">More...</div>
<div class="abs divider"></div>

<h3 class="abs h-section" style="left:614px;top:564px"><span class="dk">Book</span> Online</h3>
<div class="abs field" style="left:601px;top:604px;width:206px">Name</div>
<div class="abs field" style="left:601px;top:639px;width:206px">Email</div>
<div class="abs field" style="left:601px;top:674px;width:206px">Phone</div>
<div class="abs field" style="left:601px;top:710px;width:206px">Clinic</div>
<div class="abs pref-on">Appointment<br>Preference 1</div>
<div class="abs pref-off">Appointment<br>Preference 2</div>
<div class="abs field" style="left:606px;top:792px;width:58px">Date</div>
<div class="abs field" style="left:676px;top:792px;width:58px">Month</div>
<div class="abs field" style="left:746px;top:792px;width:59px">Time</div>
<div class="abs field" style="left:601px;top:831px;width:206px;height:63px;line-height:26px">Message</div>
<div class="abs btn-gold" style="left:672px;top:913px;width:72px;height:23px;line-height:23px">Submit</div>

<div class="abs smile" role="img" aria-label="Group of smiling friends gathered close together"></div>
<div class="abs smile-band">Gat a smile analysis</div>
<div class="abs offer"></div>
<p class="abs offer-text">Veneers, Whitening,<br>Dentures, Braces,<br>Cosmetics</p>
<div class="abs offer-band">Find out more</div>

<h4 class="abs h-foot" style="left:182px;top:973px">Quick Links</h4>
<ul class="abs links" style="left:182px;top:1019px"><li>Home</li><li>News and Events</li><li>Services</li><li>The Team</li><li>Contact Us</li></ul>
<ul class="abs links" style="left:342px;top:1019px"><li>Home</li><li>News and Events</li><li>Services</li><li>The Team</li><li>Contact Us</li></ul>

<h4 class="abs h-foot" style="left:502px;top:973px">Testimonials</h4>
<div class="abs qmark" style="left:488px;top:1000px">&ldquo;</div>
<p class="abs quote" lang="en">Sed ut perspiciatis unde omnis iste natus error sit voluptatem accusantium doloremque laudantium, totam rem aperiam, eaque ipsa voluptas sit aspernatur aut odit aut fugit, sed quia consequuntur magni dolores eos</p>
<div class="abs" style="left:700px;top:1126px;font-size:11.5px;color:#333">- marcus</div>
<div class="abs qmark" style="left:740px;top:1118px">&rdquo;</div>

<h4 class="abs h-foot" style="left:854px;top:973px">Follow us</h4>
<div class="abs social" style="top:1013px"></div><div class="abs social-name" style="top:1017px">Friendbook</div>
<div class="abs social" style="top:1061px"></div><div class="abs social-name" style="top:1065px">Chirper</div>
<div class="abs social" style="top:1109px"></div><div class="abs social-name" style="top:1113px">RSS</div>

<footer class="abs footer">Copyright &copy; 2012.www.AshfordDentalClinic.com</footer>
</body>
</html>
```